Business Card Design for Technology Company

New business card design needed for technology company director.
Ideally, the design will fit the style and nature of the industry. We are a supplier of quality products and services, and we hope the design will give customers and suppliers this impression.

Target Market(s)

3D Printing Industry

Industry/Entity Type

Technology Equipment

Contact Information for Business Card

Name: Marcus Lin
Title: Director
Company address: Factory K4, 7B Harlowe Road, Kelverton Northvale Australia 3094
Telephone: +61-3-8555 6413
Email: marcus.lin@vortalmake.com.au
Website: www.vortalmake.com.au

Requirements
Must have
• All information in business card details
• Company logo
• '3D Printers and 3D Print Filaments' at proper place
Nice to have
• Style to fit the industry
• Colour to fit logo

```html
<!DOCTYPE html>
<html lang="en">
<head>
<meta charset="utf-8">
<title>Vortal Make – Business Card</title>
<link rel="stylesheet" href="https://fonts.googleapis.com/css2?family=Roboto:wght@400;500;700&display=swap">
<style>
  :root {
    --page-bg: #ececec;
    --card-white: #ffffff;
    --card-black: #000000;
    --brand-blue: #0b4f86;
    --brand-blue-dark: #0a3f6e;
    --brand-orange: #ff8c00;
    --ink: #111111;
    --text-grey: #555555;
    --divider: #cfcfcf;
  }
  * { margin: 0; padding: 0; box-sizing: border-box; }
  html, body {
    width: 1125px;
    height: 1200px;
    overflow: hidden;
    background: var(--page-bg);
    font-family: "Roboto", Arial, sans-serif;
  }
  .card {
    position: absolute;
    left: 156px;
    width: 825px;
    height: 472px;
    overflow: hidden;
  }
  .card--front { top: 106px; background: var(--card-white); }
  .card--back { top: 639px; background: var(--card-black); }

  /* Front: brand block */
  .brand {
    position: absolute;
    left: 60px;
    width: 340px;
    top: 207px;
    display: flex;
    align-items: center;
    justify-content: center;
    gap: 12px;
  }
  .brand__square {
    width: 24px;
    height: 24px;
    background: var(--brand-orange);
  }
  .brand__name {
    font-size: 28px;
    font-weight: 700;
    letter-spacing: 3px;
    color: var(--ink);
  }
  .divider {
    position: absolute;
    left: 368px;
    top: 100px;
    width: 2px;
    height: 248px;
    background: linear-gradient(to bottom, rgba(207,207,207,0), var(--divider) 20%, var(--divider) 80%, rgba(207,207,207,0));
  }

  /* Front: contact block */
  .contact {
    position: absolute;
    left: 406px;
    top: 117px;
  }
  .contact__name {
    font-size: 31px;
    font-weight: 700;
    color: var(--brand-blue);
    line-height: 1;
  }
  .contact__title {
    margin-top: 5px;
    font-size: 20px;
    font-weight: 500;
    color: var(--brand-orange);
    line-height: 1;
  }
  .contact__address {
    margin-top: 22px;
    font-size: 19.5px;
    line-height: 25px;
    color: var(--text-grey);
  }
  .contact__line {
    display: flex;
    align-items: center;
    gap: 9px;
    font-size: 19.5px;
    color: var(--text-grey);
    line-height: 27px;
  }
  .contact__line--phone { margin-top: 10px; }
  .contact__icon { width: 19px; height: 19px; flex: none; }

  /* Front: footer band */
  .footer-line {
    position: absolute;
    left: 0;
    bottom: 0;
    width: 100%;
    height: 11px;
    background: var(--brand-orange);
  }
  .footer-tab {
    position: absolute;
    left: 190px;
    bottom: 0;
    width: 440px;
    height: 44px;
  }
  .footer-tab__url {
    position: absolute;
    left: 190px;
    bottom: 0;
    width: 440px;
    height: 44px;
    display: flex;
    align-items: center;
    justify-content: center;
    font-size: 19px;
    letter-spacing: 3.2px;
    color: var(--card-white);
  }

  /* Back */
  .back-brand {
    position: absolute;
    left: 0;
    width: 100%;
    top: 205px;
    display: flex;
    align-items: center;
    justify-content: center;
    gap: 16px;
  }
  .back-brand__square {
    width: 36px;
    height: 36px;
    background: var(--brand-orange);
  }
  .back-brand__name {
    font-size: 44px;
    font-weight: 700;
    letter-spacing: 4px;
    color: var(--card-white);
  }
  .tagline {
    position: absolute;
    left: 0;
    width: 100%;
    top: 402px;
    text-align: center;
    font-size: 20px;
    color: var(--card-white);
  }
</style>
</head>
<body>
  <section class="card card--front">
    <div class="brand">
      <span class="brand__square"></span>
      <span class="brand__name">VORTAL MAKE</span>
    </div>
    <div class="divider"></div>
    <div class="contact">
      <p class="contact__name">MARCUS LIN</p>
      <p class="contact__title">DIRECTOR</p>
      <p class="contact__address">Factory K4, 7B Harlowe Road,<br>Kelverton Northvale<br>Australia 3094</p>
      <p class="contact__line contact__line--phone">
        <svg class="contact__icon" viewBox="0 0 24 24" aria-hidden="true"><path fill="#0b4f86" d="M6.6 10.8a15.1 15.1 0 0 0 6.6 6.6l2.2-2.2c.3-.3.7-.4 1-.2 1.1.4 2.3.6 3.6.6.6 0 1 .4 1 1V20c0 .6-.4 1-1 1A17 17 0 0 1 3 4c0-.6.4-1 1-1h3.5c.6 0 1 .4 1 1 0 1.3.2 2.5.6 3.6.1.3 0 .7-.2 1z"/></svg>
        +61-3-8555 6413
      </p>
      <p class="contact__line">
        <svg class="contact__icon" viewBox="0 0 24 24" aria-hidden="true"><rect x="2" y="5" width="20" height="14" fill="#0b4f86"/><path d="M2.5 5.5 12 13l9.5-7.5" fill="none" stroke="#ffffff" stroke-width="1.8"/></svg>
        marcus.lin@vortalmake.com.au
      </p>
    </div>
    <div class="footer-line"></div>
    <svg class="footer-tab" viewBox="0 0 440 44" aria-hidden="true">
      <defs>
        <linearGradient id="tabGradient" x1="0" y1="0" x2="1" y2="0">
          <stop offset="0" stop-color="#0a3f6e"/>
          <stop offset="0.5" stop-color="#1763a3"/>
          <stop offset="1" stop-color="#0a3f6e"/>
        </linearGradient>
      </defs>
      <polygon points="0,44 36,0 404,0 440,44" fill="#ffffff"/>
      <polygon points="6,44 42,0 398,0 434,44" fill="url(#tabGradient)"/>
    </svg>
    <div class="footer-tab__url">www.vortalmake.com.au</div>
  </section>

  <section class="card card--back">
    <div class="back-brand">
      <span class="back-brand__square"></span>
      <span class="back-brand__name">VORTAL MAKE</span>
    </div>
    <p class="tagline">3D Printers and 3D Print Filaments</p>
  </section>
</body>
</html>
```